Medical VIP club - small design

Please read the specs in a design brief attached. Also we don't have logo in a Vector format and attaching the only version we have.

Club

```html
<!DOCTYPE html>
<html lang="en">
<head>
<meta charset="utf-8">
<title>Velmora – VIP Club</title>
<link rel="stylesheet" href="https://fonts.googleapis.com/css2?family=Pinyon+Script&family=Lora:ital,wght@0,400;0,600;1,400&display=swap">
<style>
  :root{
    --bg-upper:#4b2f1f;
    --bg-lower:#3a2315;
    --bg-deep:#2f1c10;
    --cream:#f4e9c3;
    --cream-light:#f9f2d8;
    --cream-edge:#e6d4a2;
    --frame:#7a5c3e;
    --frame-line:#b0926a;
    --nav:#5c412c;
    --nav-dark:#4a3322;
    --nav-text:#f4e7c8;
    --logo-brown:#6e5538;
    --caption:#7a6040;
    --caption-text:#f5e6c0;
    --white:#ffffff;
    --icon-tile:#a58a66;
  }
  html,body{margin:0;padding:0;overflow:hidden;background:var(--bg-upper)}
  .canvas{
    position:relative;width:1200px;height:729px;overflow:hidden;
    background:linear-gradient(180deg,var(--bg-upper) 0,var(--bg-upper) 516px,var(--bg-lower) 519px,var(--bg-deep) 729px);
    font-family:"Lora",Georgia,serif;
  }
  .band-line{position:absolute;left:0;top:515px;width:1200px;height:3px;background:var(--frame-line);opacity:.7}

  .site-frame{
    position:absolute;left:188px;top:17px;width:840px;height:649px;
    background:var(--frame);border:1px solid var(--frame-line);border-radius:8px;
    box-shadow:0 2px 8px rgba(0,0,0,.35);
  }
  .header{
    position:absolute;left:192px;top:21px;width:833px;height:114px;
    background:radial-gradient(ellipse at 60% 40%,var(--cream-light),var(--cream) 60%,var(--cream-edge));
    border-radius:6px 6px 0 0;
  }
  .brand{
    position:absolute;left:56px;top:52px;display:flex;align-items:center;gap:7px;
    color:var(--logo-brown);font-weight:600;font-size:25px;
  }
  .brand-dot{width:10px;height:10px;border-radius:50%;background:var(--logo-brown)}

  .nav-bar{
    position:absolute;left:178px;top:135px;width:861px;height:34px;
    background:linear-gradient(180deg,var(--nav),var(--nav-dark));
    box-shadow:0 2px 4px rgba(0,0,0,.35);
  }
  .nav{position:absolute;left:36px;top:0;height:34px;display:flex;align-items:center;margin:0;padding:0;list-style:none}
  .nav li{font-family:"Pinyon Script",cursive;font-size:16px;word-spacing:.3em;color:var(--nav-text);padding:0 9px;line-height:34px;white-space:nowrap}
  .nav li.is-active{background:rgba(255,255,255,.08);text-shadow:0 0 4px rgba(255,255,255,.5)}
  .phone{position:absolute;left:722px;top:0;height:34px;display:flex;align-items:center;gap:6px;
    font-family:"Pinyon Script",cursive;font-size:16px;color:var(--nav-text);white-space:nowrap}

  .hero{
    position:absolute;left:192px;top:176px;width:831px;height:338px;
    background:
      radial-gradient(ellipse 22% 40% at 26% 28%,#fffbee 0,#f3e4c0 45%,transparent 100%),
      radial-gradient(ellipse 40% 30% at 70% 72%,#d9ab5c 0,transparent 100%),
      linear-gradient(180deg,#e4d2aa 0%,#d2b37c 50%,#b58a50 80%,#8c6a3e 100%);
    border:1px solid var(--cream-edge);
  }
  .hero-copy{position:absolute;right:34px;top:22px;text-align:right;color:var(--white)}
  .hero-title{margin:0;font-family:"Pinyon Script",cursive;font-weight:400;font-size:50px;word-spacing:.2em;line-height:1.1;text-shadow:0 1px 3px rgba(0,0,0,.35)}
  .hero-text{margin:2px 0 0;font-style:italic;font-size:12px;line-height:1.2;text-shadow:0 1px 2px rgba(0,0,0,.45)}
  .hero-arrow{position:absolute;bottom:4px;width:42px;height:34px;border-radius:4px;display:flex;align-items:center;justify-content:center}
  .hero-arrow.prev{left:6px;opacity:.35}
  .hero-arrow.next{right:4px;background:rgba(0,0,0,.25);border:1px solid rgba(255,255,255,.4)}

  .features{position:absolute;left:197px;top:526px;display:flex;gap:7px}
  .feature{width:157px;height:127px;border:1px solid var(--frame-line);border-radius:3px;overflow:hidden;background:var(--caption)}
  .feature-photo{height:103px}
  .feature-caption{height:24px;display:flex;align-items:center;justify-content:center;
    font-family:"Pinyon Script",cursive;font-size:15px;word-spacing:.3em;color:var(--caption-text);border-top:1px solid var(--cream-edge);white-space:nowrap}
  .photo-emergency{background:linear-gradient(160deg,#e8dfcc 0%,#b3a387 40%,#7d6d54 75%,#4f4232 100%)}
  .photo-transport{background:linear-gradient(180deg,#3a79c6 0%,#5f9ade 45%,#9fc5ec 75%,#e4eef8 100%)}
  .photo-hotel{background:linear-gradient(170deg,#cfc3ad 0%,#958872 40%,#51473a 75%,#241e17 100%)}
  .photo-doctors{background:linear-gradient(160deg,#efe7d6 0%,#d9ccb2 45%,#a89675 80%,#857357 100%)}
  .photo-member{background:linear-gradient(150deg,#ede4d2 0%,#d4c6a8 50%,#a8987a 100%)}

  .footer{position:absolute;left:204px;top:688px;display:flex;align-items:center;gap:12px;color:var(--caption-text)}
  .footer-brand{font-weight:600;font-size:13px;color:var(--icon-tile)}
  .footer-note{font-size:11px}
  .social{position:absolute;left:903px;top:683px;display:flex;gap:6px}
  .social span{width:32px;height:32px;border-radius:4px;background:var(--icon-tile);border:1px solid #c6ad86}
</style>
</head>
<body>
<div class="canvas">
  <div class="band-line"></div>
  <div class="site-frame"></div>

  <header class="header">
    <div class="brand"><span class="brand-dot"></span>Velmora</div>
  </header>

  <nav class="nav-bar">
    <ul class="nav">
      <li>About Us</li>
      <li>VIP Club</li>
      <li>Services</li>
      <li>Package and Prices</li>
      <li class="is-active">Registration</li>
      <li>Contact</li>
    </ul>
    <div class="phone">
      <svg width="13" height="14" viewBox="0 0 24 24" aria-hidden="true"><path fill="#f4e7c8" d="M6.6 10.8a15.1 15.1 0 0 0 6.6 6.6l2.2-2.2c.3-.3.7-.4 1-.2 1.1.4 2.3.6 3.6.6.6 0 1 .4 1 1V20c0 .6-.4 1-1 1A17 17 0 0 1 3 4c0-.6.4-1 1-1h3.5c.6 0 1 .4 1 1 0 1.3.2 2.5.6 3.6.1.3 0 .7-.2 1z"/></svg>
      555-014-200
    </div>
  </nav>

  <section class="hero" role="img" aria-label="Luxurious hotel suite with a golden bed, draped curtains and a chandelier">
    <div class="hero-copy">
      <h1 class="hero-title">VIP Club</h1>
      <p class="hero-text">Lorem Ipsum is simply dummy text of the<br>printing and typesetting industry</p>
    </div>
    <div class="hero-arrow prev">
      <svg width="22" height="24" viewBox="0 0 22 24" aria-hidden="true"><path d="M20 2 L2 12 L20 22 Z" fill="#fff"/></svg>
    </div>
    <div class="hero-arrow next">
      <svg width="22" height="24" viewBox="0 0 22 24" aria-hidden="true"><path d="M2 2 L20 12 L2 22 Z" fill="#fff"/></svg>
    </div>
  </section>

  <section class="features">
    <article class="feature"><div class="feature-photo photo-emergency" role="img" aria-label="Hospital building with emergency signs"></div><div class="feature-caption">Emergency Plan</div></article>
    <article class="feature"><div class="feature-photo photo-transport" role="img" aria-label="Passenger airplane in a blue sky"></div><div class="feature-caption">Transportation</div></article>
    <article class="feature"><div class="feature-photo photo-hotel" role="img" aria-label="Hotel reception desk bell"></div><div class="feature-caption">Hotel Services</div></article>
    <article class="feature"><div class="feature-photo photo-doctors" role="img" aria-label="Team of medical staff"></div><div class="feature-caption">Variety of Doctors</div></article>
    <article class="feature"><div class="feature-photo photo-member" role="img" aria-label="Hand signing a membership form"></div><div class="feature-caption">Become a Member</div></article>
  </section>

  <footer class="footer">
    <span class="footer-brand">Velmora</span>
    <span class="footer-note">© Velmora 2010. All rights reserved.</span>
  </footer>
  <div class="social" aria-label="Social links">
    <span></span><span></span><span></span>
  </div>
</div>
</body>
</html>
```